Corporate Travel Technology Company needs new Business Card design

We need a new business card design to reflect our re-branded company. Our company is called tolvEn (pronounced tolvenn) and we provide Business Intelligence and mobile travel management solutions for the corporate travel industry. Our multinational customers use our solutions to manage large travel budgets and frequent travellers, as well as to save money and reduce risk. We'd like to see designs that use the blue and green palette as well as our corporate logo (attached below). The design should communicate innovation, insight, forward thinking, contemporary, trusted.

Target Market(s)

Large multinational corporates and Travel Agencies.

Industry/Entity Type

Business

Contact Information for Business Card

Rosalind Mercer
Chief Executive
tolvEn
Phone number - +61 (0)2 8134 2907
Email address - rosalind.mercer@tolven-example.com
Mobile number - +61 (0)438 516 702
www.tolven-example.com

Font styles to use
Other font styles liked:
• Please use font as close to corporate logo as possible

Colors
0255a3
0393ce
00a990
33b8a4
33a6d7
3176b5

Requirements
Must have
• Please include the words;
• Mobile Travel Management
• Accelerating Travel Business Insights
• Use corporate logo - although icon can be stylised if needed

```html
<!DOCTYPE html>
<html lang="en">
<head>
<meta charset="utf-8">
<title>tolvEn business card</title>
<link rel="stylesheet" href="https://fonts.googleapis.com/css2?family=Roboto:wght@400;700&family=Open+Sans:wght@400&display=swap">
<style>
  :root {
    --backdrop: #d2d3d4;
    --paper: #ffffff;
    --band: #58585a;
    --band-pattern: #606062;
    --brand-blue: #0a55a3;
    --brand-ink: #3f5b58;
    --text-light: #ffffff;
    --ring: rgba(120, 170, 225, 0.55);
  }
  * { margin: 0; padding: 0; box-sizing: border-box; }
  html, body {
    width: 1200px; height: 440px; overflow: hidden;
    background: var(--backdrop);
  }
  .stage { position: relative; width: 1200px; height: 440px; }
  .card {
    position: absolute; width: 555px; height: 371px;
    background: var(--paper); overflow: hidden;
  }
  .card--front { left: 31px; top: 31px; }
  .card--back { left: 619px; top: 35px; }

  .band {
    position: absolute; left: 0; right: 0; bottom: 0;
    background: var(--band);
  }
  .card--front .band { height: 109px; }
  .card--back .band { height: 169px; }

  .wordmark {
    position: absolute; display: flex; align-items: center; gap: 8px;
    font-family: "Roboto", sans-serif; font-weight: 400;
    color: var(--brand-ink); letter-spacing: 0.5px; line-height: 1;
  }
  .wordmark__dot {
    display: block; border-radius: 50%; background: var(--brand-ink);
  }
  .card--front .wordmark { left: 50%; top: 140px; transform: translateX(-50%); font-size: 54px; }
  .card--front .wordmark__dot { width: 14px; height: 14px; }
  .card--back .wordmark { left: 129px; top: 88px; transform: translateX(-50%); font-size: 44px; }
  .card--back .wordmark__dot { width: 11px; height: 11px; }

  .tagline {
    position: absolute; left: 0; right: 0; top: 295px;
    text-align: center; color: var(--text-light);
    font-family: "Roboto", sans-serif; font-size: 15px; line-height: 22px;
  }

  .name-column {
    position: absolute; left: 296px; top: 0; width: 183px; height: 371px;
    background: var(--brand-blue); text-align: center; color: var(--text-light);
    overflow: hidden;
  }
  .person__name {
    margin-top: 76px;
    font-family: "Roboto", sans-serif; font-weight: 700; font-size: 18px; letter-spacing: 0.2px;
  }
  .person__role {
    margin-top: 2px;
    font-family: "Roboto", sans-serif; font-size: 14px;
  }
  .name-column__ring {
    position: absolute; left: 27px; top: 183px;
  }

  .contact {
    position: absolute; left: 40px; list-style: none;
    font-family: "Open Sans", sans-serif; color: var(--text-light);
  }
  .contact__item { position: absolute; left: 0; display: flex; align-items: center; gap: 14px; white-space: nowrap; }
  .contact__item--phone { top: 220px; }
  .contact__item--email { top: 274px; }
  .contact__item--web { top: 323px; }
  .contact__icon { width: 26px; flex: none; display: flex; justify-content: center; }
  .contact__text { font-size: 13px; line-height: 16px; }
  .contact__item--email .contact__text { font-size: 12px; }
</style>
</head>
<body>
<main class="stage">

  <section class="card card--front" aria-label="Card front">
    <div class="wordmark"><span>tolvEn</span><span class="wordmark__dot"></span></div>
    <div class="band">
    </div>
    <p class="tagline">Mobile Travel Management<br>Accelerating Travel Business Insights</p>
  </section>

  <section class="card card--back" aria-label="Card back">
    <div class="wordmark"><span>tolvEn</span><span class="wordmark__dot"></span></div>
    <div class="band"></div>

    <ul class="contact">
      <li class="contact__item contact__item--phone">
        <span class="contact__icon">
          <svg width="22" height="22" viewBox="0 0 24 24" aria-hidden="true"><path fill="#fff" d="M6.6 10.8a15.1 15.1 0 0 0 6.6 6.6l2.2-2.2c.3-.3.7-.4 1-.2 1.1.4 2.3.6 3.6.6.6 0 1 .4 1 1V20c0 .6-.4 1-1 1A17 17 0 0 1 3 4c0-.6.4-1 1-1h3.5c.6 0 1 .4 1 1 0 1.3.2 2.5.6 3.6.1.3 0 .7-.2 1z"/></svg>
        </span>
        <span class="contact__text">+61 (0)2 8134 2907<br>+61 (0)438 516 702</span>
      </li>
      <li class="contact__item contact__item--email">
        <span class="contact__icon">
          <svg width="26" height="18" viewBox="0 0 26 18" aria-hidden="true"><rect x="0" y="0" width="26" height="18" fill="#fff"/><path d="M1 1l12 9 12-9" fill="none" stroke="#58585a" stroke-width="1.6"/></svg>
        </span>
        <span class="contact__text">rosalind.mercer@tolven-example.com</span>
      </li>
      <li class="contact__item contact__item--web">
        <span class="contact__icon">
          <svg width="26" height="26" viewBox="0 0 26 26" aria-hidden="true"><g fill="none" stroke="#fff" stroke-width="1.8"><circle cx="13" cy="13" r="11.5"/><ellipse cx="13" cy="13" rx="5" ry="11.5"/><path d="M1.5 13h23M3.5 7h19M3.5 19h19"/></g></svg>
        </span>
        <span class="contact__text">www.tolven-example.com</span>
      </li>
    </ul>

    <div class="name-column">
      <p class="person__name">ROSALIND MERCER</p>
      <p class="person__role">Chief Executive</p>
      <svg class="name-column__ring" width="130" height="130" viewBox="0 0 130 130" aria-hidden="true">
        <circle cx="65" cy="65" r="58" fill="none" stroke="var(--ring)" stroke-width="8"/>
      </svg>
    </div>
  </section>

</main>
</body>
</html>
```